Kestrelway Financial Plans

I am looking for a complete resdesign of my small financial presentation. This is a Word Doc/PDF that I print off when meeting with people in private. I often present my "two pager" that I have been using for years and years. It tells them the basics of what I do, how I help people and foundational financial principles.

I have recently gone out on my own in business and have completely rebranded. This presentation is my most used tool, so it is the first of many things I would like to redo. I am hoping it will somehow coordinate with the colors of my business, not necessarily the EXACT same 3 colors everywhere, but have the design colors compliment.

I've uploaded all my logo designs, as well as the current "two-pager". I am not against it going to 3 pages if needed. As it will still land on 2 pages with duplex printing.

It has always been VERY simple. I am wanting it built into a more professional and design specific format, to show off my branding, without being over cluttered.

I am completely open to ANY graphics changes. Obviously some are very novice, the house on the last page has always been overly simplified.

```html
<!DOCTYPE html>
<html lang="en">
<head>
<meta charset="utf-8">
<title>Kestrelway Financial Plans – Client Overview</title>
<link rel="stylesheet" href="https://fonts.googleapis.com/css2?family=Montserrat:wght@300;400;500;600;700;800&display=swap">
<style>
:root{
  --navy:#0f2233;
  --green:#1aa33a;
  --mint:#b9f5c9;
  --mint-pale:#e7fbee;
  --slate:#4a5568;
  --grey:#a9aeb3;
  --grey-light:#e3e5e7;
  --rule:#cfd3d6;
  --red:#e0201b;
  --bg:#ebecee;
  --paper:#ffffff;
}
*{box-sizing:border-box;margin:0;padding:0}
html,body{width:1200px;height:2335px;overflow:hidden}
body{background:var(--bg);font-family:"Montserrat",sans-serif;color:var(--navy);
  display:flex;flex-direction:column;align-items:center;justify-content:center;gap:40px}
.row{display:flex;gap:30px}
.page{position:relative;width:560px;height:792px;background:var(--paper);
  box-shadow:0 2px 8px rgba(0,0,0,.12);overflow:hidden}
.abs{position:absolute}

/* header */
.top-band{position:absolute;left:0;top:0;width:100%;height:22px;background:var(--mint-pale)}
.brand-tab{position:absolute;left:69px;top:0;width:133px;height:52px;background:#fff;
  border-bottom:3px solid var(--navy);display:flex;flex-direction:column;align-items:center;justify-content:center}
.brand-name{font-weight:700;color:var(--navy);font-size:14px;letter-spacing:.5px;line-height:1}
.brand-sub{font-weight:700;color:var(--navy);font-size:5.5px;letter-spacing:1.2px;margin-top:3px}
.section-band{position:absolute;height:24px;background:var(--mint);display:flex;align-items:center;
  justify-content:center;font-size:14px;font-weight:400;letter-spacing:.4px;color:var(--navy);text-transform:uppercase}
.page-num{position:absolute;left:63px;top:744px;font-size:7.5px;color:var(--navy)}

/* cover */
.cover-brand{position:absolute;left:76px;top:372px}
.cover-brand .brand-name{font-size:30px;letter-spacing:1px}
.cover-brand .brand-sub{font-size:10px;letter-spacing:2.5px;margin-top:6px;padding-left:32px}
.cover-title{position:absolute;left:69px;top:468px;font-weight:800;font-size:57px;line-height:1.05}
.cover-title .accent{color:var(--green);display:block}
.cover-rule{position:absolute;left:69px;right:0;top:611px;height:3px;background:var(--navy)}
.cover-date{position:absolute;left:69px;top:634px;font-size:19px;font-weight:400}

/* challenge */
.fact-row{position:absolute;left:62px;width:428px;border-bottom:1px solid var(--rule)}
.fact-label{position:absolute;left:8px;font-size:10px;font-weight:700;color:var(--green)}
.fact-icon{position:absolute;left:12px}
.fact-text{position:absolute;left:106px;width:318px;font-size:6.6px;line-height:1.25}
.fact-text p{margin-bottom:5px}
.fact-text .src{color:var(--green)}

/* pillars */
.pillar-line{position:absolute;height:2px;background:var(--green)}
.pillar{position:absolute;width:136px;height:38px;display:flex;flex-direction:column;align-items:center;
  justify-content:flex-end;text-align:center;font-size:7.5px;font-weight:700;line-height:1.15}
.pillar svg{display:block;margin:0 auto 4px;flex:none}
.edu-bar{position:absolute;left:67px;width:426px;top:506px;height:20px;background:var(--grey-light);
  font-size:7.5px;font-weight:700;display:flex;align-items:center;justify-content:center}

/* how */
.checklist{position:absolute;left:232px;top:596px;list-style:none}
.checklist li{display:flex;align-items:center;font-size:6.5px;font-weight:700;height:34.5px}
.checklist li::before{content:"";width:9px;height:9px;border:1.3px solid var(--green);margin-right:7px}
.flow-label{position:absolute;font-size:8px;font-weight:700}
.chev{position:absolute}
.partners{position:absolute;left:370px;top:584px;display:grid;grid-template-columns:60px 60px;gap:4px}
.partner{height:24px;background:#fff;border:1px solid var(--grey-light);display:flex;align-items:center;
  justify-content:center;font-size:6px;font-weight:600;color:var(--navy);white-space:nowrap}

/* rule of 72 */
.rate-table{position:absolute;top:104px;width:99px}
.rate-head{display:flex;height:24px}
.rate-head span{flex:1;display:flex;align-items:center;justify-content:center;font-size:8.5px;font-weight:700;color:#fff}
.rate-head .age{background:var(--green)}
.rate-head .pct{background:var(--navy)}
.rate-row{display:flex;height:20px;border-bottom:1px solid var(--rule);font-size:7px}
.rate-row span{flex:1;display:flex;align-items:center;justify-content:center}
.doubles{position:absolute;top:252px;width:99px;text-align:center;font-size:7px;font-weight:700;line-height:1.15}

/* taxes house */
.column{position:absolute;top:434px;width:96px;height:136px;background:#f4f5f6}
.column-head{height:57px;color:#fff;display:flex;flex-direction:column;align-items:center;justify-content:flex-end;
  padding-bottom:6px;font-size:9.5px;font-weight:700}
.column-head svg{margin-bottom:4px}
.column-head.navy{background:var(--navy)}
.column-head.green{background:var(--green)}
.column-body{padding:6px 4px;text-align:center;font-size:6px;font-weight:700;line-height:1.2}
.column-body p{margin-bottom:7px}
.tax-tag{position:absolute;top:571px;width:64px;height:22px;background:var(--grey-light);
  display:flex;align-items:center;justify-content:center;font-size:8px;font-weight:700;color:var(--red)}
.foundation{position:absolute;left:91px;top:605px;width:395px;height:44px;border-radius:22px;background:var(--grey);
  display:flex;justify-content:space-around;align-items:center;color:#fff;font-size:7px;font-weight:700;text-align:center}
.foundation div{line-height:1}
.foundation hr{border:0;border-top:1px solid #fff;width:128px;margin:4px auto}
</style>
</head>
<body>

<div class="row">
  <section class="page cover">
    <div class="cover-brand">
      <div class="brand-name">KESTRELWAY</div>
      <div class="brand-sub">FINANCIAL PLANS</div>
    </div>
    <h1 class="cover-title"><span class="accent">Document</span>Title Here</h1>
    <div class="cover-rule"></div>
    <div class="cover-date">December 2024</div>
  </section>

  <section class="page">
    <div class="top-band"></div>
    <div class="brand-tab"><div class="brand-name">KESTRELWAY</div><div class="brand-sub">FINANCIAL PLANS</div></div>

    <div class="section-band" style="left:60px;width:426px;top:71px">The Financial Challenge</div>

    <div class="fact-row" style="top:102px;height:66px">
      <svg class="fact-icon" style="top:6px" width="28" height="26" viewBox="0 0 28 26" fill="none" stroke="#0f2233" stroke-width="1.3"><ellipse cx="14" cy="15" rx="10" ry="7"/><circle cx="14" cy="6" r="3.5"/><path d="M8 21v3M20 21v3"/></svg>
      <div class="fact-label" style="top:44px">SAVINGS</div>
      <div class="fact-text" style="top:4px">
        <p>49% of canadian employees are living paycheque to paycheque. 25% of canadians are unable to cover an unexpected $500 expense<br><span class="src">• Canadian Statistics Office (feb 2023)</span></p>
        <p>25% of canadians need to access their retirement savings early. 20% of canadians have no savings. 39% of canadians aged 55-65 have less than $5,000 in savings.<br><span class="src">• National Savings Survey (june 2023)</span></p>
      </div>
    </div>

    <div class="fact-row" style="top:172px;height:68px">
      <svg class="fact-icon" style="top:6px" width="28" height="28" viewBox="0 0 28 28" fill="none" stroke="#0f2233" stroke-width="1.3"><path d="M9 4h10l-3 5h-4z"/><path d="M12 9c-6 4-7 15 2 15s8-11 2-15"/><path d="M14 13v8M12 15h3a1.5 1.5 0 010 3h-2a1.5 1.5 0 000 3h3"/></svg>
      <div class="fact-label" style="top:46px">DEBT</div>
      <div class="fact-text" style="top:4px">
        <p>The average canadian has $22,131 in consumer debt. Which excludes mortgages.<br><span>• Creditline Bureau (aug 2024)</span></p>
        <p>Over 55% of canadians hold credit card debt and the total canadian household debt has increased to $2.52trillion, including consumer credit, mortgage and non-mortgage loans.<br><span class="src">• National Lenders Assoc. (aug 2024)</span></p>
      </div>
    </div>

    <div class="fact-row" style="top:244px;height:70px;border:0">
      <svg class="fact-icon" style="top:6px" width="26" height="28" viewBox="0 0 26 28" fill="none" stroke="#0f2233" stroke-width="1.3"><rect x="4" y="4" width="16" height="21" rx="1"/><path d="M9 2h6v4H9zM8 11h8M8 15h8"/><path d="M17 18l3-1 3 1v3c0 2-3 3.5-3 3.5s-3-1.5-3-3.5z"/></svg>
      <div class="fact-label" style="top:46px">INSURANCE</div>
      <div class="fact-text" style="top:4px">
        <p>45% of canadians do not have individual life insurance coverage, but 48% say their families would face financial trouble within 6 months of losing someone.<br><span class="src">• Lifeline Research Intl. (apr 2023)</span></p>
        <p>2-in-5 canadians (43% women / 44% men) will be diagosed with a form of cancer or other critical illness during their lifetime. Every 7 seconds.<br><span class="src">• Public Health Data Hub (june 2024)</span></p>
      </div>
    </div>

    <div class="section-band" style="left:67px;width:426px;top:331px">Who Are We And What Do We Do?</div>

    <div class="pillar" style="left:67px;top:366px"><svg width="20" height="18" viewBox="0 0 20 18" fill="none" stroke="#0f2233" stroke-width="1.2"><circle cx="10" cy="9" r="6"/><path d="M2 6a8 8 0 0114-3M18 12a8 8 0 01-14 3"/></svg>CASH<br>FLOW</div>
    <div class="pillar" style="left:212px;top:366px"><svg width="18" height="18" viewBox="0 0 18 18" fill="none" stroke="#0f2233" stroke-width="1.2"><rect x="3" y="2" width="12" height="14"/><path d="M6 6h6M6 9h6M6 12h4"/></svg>DEBT<br>MANAGEMENT</div>
    <div class="pillar" style="left:357px;top:366px"><svg width="18" height="18" viewBox="0 0 18 18" fill="none" stroke="#0f2233" stroke-width="1.2"><circle cx="9" cy="6" r="4"/><path d="M3 16c1-4 11-4 12 0"/></svg>BUILD<br>WEALTH</div>

    <div class="pillar-line" style="left:67px;width:136px;top:409px"></div>
    <div class="pillar-line" style="left:210px;width:140px;top:409px"></div>
    <div class="pillar-line" style="left:357px;width:136px;top:409px"></div>

    <div class="pillar" style="left:67px;top:428px"><svg width="18" height="18" viewBox="0 0 18 18" fill="none" stroke="#0f2233" stroke-width="1.2"><circle cx="9" cy="8" r="6"/><path d="M3 8h12M9 2v12M5 16h8"/></svg>CASH FLOW<br>PROTECTION</div>
    <div class="pillar" style="left:212px;top:428px"><svg width="18" height="18" viewBox="0 0 18 18" fill="none" stroke="#0f2233" stroke-width="1.2"><path d="M2 9a7 7 0 0114 0z"/><path d="M9 9v6a2 2 0 01-3 0"/></svg>EMERGENCY<br>FUND</div>
    <div class="pillar" style="left:357px;top:428px"><svg width="20" height="14" viewBox="0 0 20 14" fill="none" stroke="#0f2233" stroke-width="1.2"><path d="M1 7h5l4-3h6v6h-6l-4-2"/><rect x="16" y="3" width="3" height="8"/></svg>PRESERVE</div>

    <div class="pillar-line" style="left:67px;width:136px;top:471px"></div>
    <div class="pillar-line" style="left:210px;width:140px;top:471px"></div>
    <div class="pillar-line" style="left:357px;width:136px;top:471px"></div>

    <div class="edu-bar">EDUCATION &amp; AWARENESS</div>

    <div class="section-band" style="left:67px;width:426px;top:548px">How Are We Doing It</div>

    <svg class="abs" style="left:59px;top:588px" width="124" height="124" viewBox="0 0 124 124" role="img" aria-label="Pie chart of income split between living expenses, taxes and debt">
      <path d="M62 62 L62 1 A61 61 0 0 0 62 123 Z" fill="#4a5568"/>
      <path d="M62 62 L62 1 A61 61 0 0 1 123 62 Z" fill="#0f2233"/>
      <path d="M62 62 L123 62 A61 61 0 0 1 62 123 Z" fill="#1aa33a"/>
      <path d="M62 0v124M62 62h62" stroke="#fff" stroke-width="2"/>
      <text x="32" y="73" fill="#fff" font-family="Montserrat,sans-serif" font-size="7" font-weight="600" text-anchor="middle">Living</text>
      <text x="32" y="82" fill="#fff" font-family="Montserrat,sans-serif" font-size="7" font-weight="600" text-anchor="middle">Expenses</text>
      <text x="82" y="52" fill="#fff" font-family="Montserrat,sans-serif" font-size="7" font-weight="600">Taxes</text>
      <text x="80" y="97" fill="#fff" font-family="Montserrat,sans-serif" font-size="7" font-weight="600">Debt</text>
    </svg>
    <div class="flow-label" style="left:185px;top:632px">SAVINGS</div>
    <svg class="chev" style="left:200px;top:646px" width="9" height="12" viewBox="0 0 9 12"><path d="M1 1l6 5-6 5" fill="none" stroke="#0f2233" stroke-width="2.4"/></svg>

    <ul class="checklist">
      <li>RETIREMENT SAVINGS</li>
      <li>CHILDRREN'S EDUCATION</li>
      <li>PROPER PROTECTION</li>
      <li>FREEDOM FROM DEBT</li>
    </ul>
    <svg class="chev" style="left:355px;top:644px" width="9" height="12" viewBox="0 0 9 12"><path d="M1 1l6 5-6 5" fill="none" stroke="#0f2233" stroke-width="2.4"/></svg>

    <div class="partners">
      <div class="partner">Maplecrest</div><div class="partner">Northleaf Life</div>
      <div class="partner">Sunridge Life</div><div class="partner">Riverside Mutual</div>
      <div class="partner">Aurora Group</div><div class="partner">Granite Ins.</div>
      <div class="partner">Benwick</div><div class="partner">Pinefield</div>
      <div class="partner">Co-Harbor</div><div class="partner">Ivenna</div>
    </div>

    <div class="page-num">Page | 2</div>
  </section>
</div>

<section class="page">
  <div class="top-band"></div>
  <div class="brand-tab"><div class="brand-name">KESTRELWAY</div><div class="brand-sub">FINANCIAL PLANS</div></div>

  <div class="section-band" style="left:68px;width:425px;top:68px">Rule Of 72</div>

  <div class="rate-table" style="left:68px">
    <div class="rate-head"><span class="age">AGE</span><span class="pct">4%</span></div>
    <div class="rate-row"><span>29</span><span>$10,000</span></div>
    <div class="rate-row"><span>47</span><span>$20,000</span></div>
    <div class="rate-row"><span>65</span><span>$40,000</span></div>
  </div>
  <div class="rate-table" style="left:174px">
    <div class="rate-head"><span class="age">AGE</span><span class="pct">6%</span></div>
    <div class="rate-row"><span>29</span><span>$10,000</span></div>
    <div class="rate-row"><span>41</span><span>$20,000</span></div>
    <div class="rate-row"><span>53</span><span>$40,000</span></div>
    <div class="rate-row"><span>65</span><span>$80,000</span></div>
  </div>
  <div class="rate-table" style="left:280px">
    <div class="rate-head"><span class="age">AGE</span><span class="pct">8%</span></div>
    <div class="rate-row"><span>29</span><span>$10,000</span></div>
    <div class="rate-row"><span>38</span><span>$20,000</span></div>
    <div class="rate-row"><span>47</span><span>$40,000</span></div>
    <div class="rate-row"><span>56</span><span>$80,000</span></div>
    <div class="rate-row"><span>65</span><span>$160,000</span></div>
  </div>
  <div class="rate-table" style="left:386px">
    <div class="rate-head"><span class="age">AGE</span><span class="pct">12%</span></div>
    <div class="rate-row"><span>29</span><span>$10,000</span></div>
    <div class="rate-row"><span>35</span><span>$20,000</span></div>
    <div class="rate-row"><span>41</span><span>$40,000</span></div>
    <div class="rate-row"><span>47</span><span>$80,000</span></div>
    <div class="rate-row"><span>53</span><span>$160,000</span></div>
    <div class="rate-row" style="border:0"><span>59</span><span>$320,000</span></div>
  </div>

  <div class="doubles" style="left:68px">MONEY DOUBLES<br>EVERY 18 YEARS</div>
  <div class="doubles" style="left:174px">MONEY DOUBLES<br>EVERY 12 YEARS</div>
  <div class="doubles" style="left:280px">MONEY DOUBLES<br>EVERY 9 YEARS</div>
  <div class="doubles" style="left:386px">MONEY DOUBLES<br>EVERY 6 YEARS</div>

  <div class="section-band" style="left:68px;width:425px;top:316px">Taxes</div>

  <svg class="abs" style="left:68px;top:352px" width="444" height="80" viewBox="0 0 444 80">
    <path d="M42 38 L214 2 L386 38 Z" fill="#a9aeb3"/>
    <rect x="0" y="38" width="444" height="5" fill="#a9aeb3"/>
    <rect x="23" y="46" width="394" height="9" fill="#d4d7da"/>
    <rect x="23" y="58" width="394" height="9" fill="#e3e5e7"/>
  </svg>

  <div class="column" style="left:83px">
    <div class="column-head navy"><svg width="16" height="15" viewBox="0 0 16 15" fill="none" stroke="#fff" stroke-width="1.3"><path d="M1 7l7-6 7 6M3 6v8h10V6"/></svg>HOME</div>
    <div class="column-body"><p>PARTNER WITH MORTGAGE BROKERS FOR BEST RATES</p><p>MORTGAGE INSURANCE ALTERNATIVES</p></div>
  </div>
  <div class="column" style="left:188px">
    <div class="column-head green"><svg width="18" height="15" viewBox="0 0 18 15" fill="none" stroke="#fff" stroke-width="1.3"><ellipse cx="9" cy="9" rx="7" ry="5"/><circle cx="9" cy="3" r="2"/></svg>RRSP</div>
    <div class="column-body"><p>TAX DEDUCTION</p><p>TAX DEFERRED</p></div>
  </div>
  <div class="column" style="left:293px">
    <div class="column-head navy"><svg width="16" height="16" viewBox="0 0 16 16" fill="none" stroke="#fff" stroke-width="1.3"><path d="M1 5l7-4 7 4zM3 6v6M8 6v6M13 6v6M1 14h14"/></svg>TFSA</div>
    <div class="column-body"><p>NO TAX DEDUCTIONS</p><p>TAX FREE GROWTH</p><p>2009-$95,000</p><p>LIMIT 2023-$7,000/YR</p></div>
  </div>
  <div class="column" style="left:398px">
    <div class="column-head green"><svg width="18" height="15" viewBox="0 0 18 15" fill="none" stroke="#fff" stroke-width="1.3"><path d="M2 7a7 6 0 0114 0z"/><circle cx="6" cy="11" r="1.6"/><circle cx="12" cy="11" r="1.6"/></svg>PERM LIFE</div>
    <div class="column-body"><p>NO TAX DEDUCTION</p><p>QUALIFY</p><p>TAX DEFERRED GROWTH</p></div>
  </div>

  <div class="tax-tag" style="left:99px">SELL</div>
  <div class="tax-tag" style="left:204px">100% TAX</div>
  <div class="tax-tag" style="left:309px">0% TAX</div>
  <div class="tax-tag" style="left:414px">0% TAX</div>

  <div class="foundation">
    <div>LIFE INSURANCE ILLNESS<hr>CRITICAL/DISABILITY</div>
    <div>DEBT MANAGEMENT<hr>CASH FLOW</div>
  </div>

  <div class="page-num">Page | 3</div>
</section>

</body>
</html>
```